Website Development for vaultmerrow.com.au

Build a new Wordpress/Responsive website for vaultmerrow.com.au

Target Market(s)

Compliance Managers, Risk Managers, Information Security and Cyber Security Professionals, Chief Data/Digital Officers, Chief Operating/Financial Officers, Business Continuity Professionals, Disaster Recovery Planners, Small Business Owners, Local/Federal Government entities

Industry/Entity Type

Data Service

Coding

Coded - Design and coding required

Number of Pages Required

5+ page

Font styles to use
Sans Serif

Colors

Designer to choose colors to be used in the design.

Requirements
Must have
• 1. Site Structure: Home Page plus the following chapter-pages for a) Services b) About c) Resources d) Blog e) Contact Us
• 2. Prefer site to built on wordpress and we can purchase a theme if needed (we currently use Kelp9 for other sites)
• 3. Blog needs to be wordpress based
• 4. We will host the site ourselves on our own servers
• 5. Responsive Design
Nice to have
• 1. Livechat capability/interface
• 2. Capability for marketing automation integration (such as hubspot, marketo, infusionsoft etc)
• 3. Capability for CRM integration (Salesforce)

```html
<!DOCTYPE html>
<html lang="en">
<head>
<meta charset="utf-8">
<title>Vault Merrow — Data Services</title>
<link rel="stylesheet" href="https://fonts.googleapis.com/css2?family=Mulish:wght@400;600;700&family=Roboto:wght@400;500;700&display=swap">
<style>
:root{
  --brand:#1565c0;
  --brand-dark:#0b3f86;
  --navy:#06152f;
  --sky:#e8f1fb;
  --ink:#222831;
  --muted:#6b7280;
  --line:#d6dde6;
  --grey:#8f959c;
  --white:#ffffff;
}
*{box-sizing:border-box;margin:0;padding:0}
html,body{width:1200px;height:4433px;overflow:hidden}
body{font-family:"Mulish",Arial,sans-serif;color:var(--ink);background:var(--white);position:relative}
.sec{position:absolute;left:0;width:1200px;overflow:hidden}
.abs{position:absolute}
h2.title{font-family:"Roboto",Arial,sans-serif;font-weight:500;font-size:40px;text-align:center;color:var(--ink);letter-spacing:.5px}
.intro{font-size:13px;line-height:29px;text-align:center;color:var(--muted)}
.intro b{color:var(--brand);font-weight:600}

/* top bar */
.topbar{top:0;height:53px;background:var(--brand)}
.topbar .contact{left:142px;top:0;height:53px;display:flex;align-items:center;gap:40px;color:#fff;font-size:14px}
.topbar .contact span{display:flex;align-items:center;gap:10px}
.topbar .follow{right:142px;top:0;height:53px;display:flex;align-items:center;gap:8px;color:#fff;font-size:14px;font-weight:700}
.social{width:20px;height:20px;border-radius:3px;background:#fff;opacity:.85}
.social:first-of-type{margin-left:10px}

/* nav */
.nav{top:53px;height:86px;background:#fff;box-shadow:0 2px 8px rgba(0,0,0,.08);z-index:3}
.brand{display:flex;align-items:center;gap:10px;font-family:"Mulish",sans-serif;font-weight:700;color:var(--brand)}
.brand .mark{border-radius:50%;background:var(--brand)}
.nav .brand{left:142px;top:22px;font-size:28px}
.nav .brand .mark{width:40px;height:40px}
.menu{right:142px;top:0;height:86px;display:flex;gap:34px;align-items:center;font-family:"Roboto",sans-serif;font-size:14px;font-weight:500;color:#333}
.menu a{color:inherit;text-decoration:none;padding:32px 0}
.menu a.active{color:var(--brand);border-bottom:3px solid var(--brand);border-top:3px solid var(--brand)}

/* hero */
.hero{top:139px;height:576px;background:radial-gradient(ellipse at 30% 40%,#2b8ae6 0%,#0d3f8f 35%,var(--navy) 75%)}
.hero .art{left:0;top:0;width:1200px;height:576px}
.hero h1{right:142px;top:222px;width:520px;text-align:right;color:#fff;font-family:"Roboto",sans-serif;font-weight:500;font-size:38px;line-height:46px}
.btn-light{right:145px;top:343px;width:177px;height:38px;background:#fff;color:var(--brand);font-family:"Roboto",sans-serif;font-weight:500;font-size:16px;display:flex;align-items:center;justify-content:center}
.dots{left:558px;top:502px;display:flex;gap:6px}
.dots i{display:block;width:22px;height:4px;background:rgba(255,255,255,.45)}
.dots i.on{background:#fff}

/* about */
.about{top:715px;height:577px;background:#fff}
.about .photo{left:142px;top:47px;width:446px;height:447px;background:linear-gradient(135deg,#dfe4ea,#8d97a3 60%,#4a5563)}
.about .photo-tag{left:154px;top:57px;color:#fff;font-weight:700;font-size:16px}
.about .head{left:630px;top:78px;display:flex;align-items:center;gap:14px;font-family:"Roboto",sans-serif;font-size:32px;font-weight:500;color:#333}
.about .head .brand{font-size:34px}
.about .head .brand .mark{width:38px;height:38px}
.about .copy{left:628px;top:172px;width:430px;font-size:12.5px;line-height:20px;color:#444}
.about .copy p{margin-bottom:10px}
.about .copy b{color:var(--brand);font-weight:600}
.about .copy .cta{font-weight:700;color:#222;font-size:13.5px}
.about .copy .cta span{color:var(--brand);font-weight:400}

/* services */
.services{top:1292px;height:573px;background:var(--sky)}
.services h2{position:absolute;top:50px;width:100%}
.services .intro{position:absolute;top:115px;width:100%}
.svc-icon{width:118px;height:118px;border-radius:50%;border:5px solid #5a5f66;background:#fff;display:flex;align-items:center;justify-content:center}
.svc-icon.on{border-color:var(--brand);box-shadow:0 0 0 8px rgba(21,101,192,.15)}
.svc-label{font-family:"Mulish",sans-serif;font-weight:600;font-size:19px;line-height:27px;color:#333}
.svc-label.on{color:var(--brand)}
.svc-label.l{text-align:right;width:260px}
.centre-mark{left:512px;top:236px;width:176px;height:176px;border-radius:50%;background:var(--brand);display:flex;align-items:center;justify-content:center;color:#fff;font-weight:700;font-size:22px}

/* audience */
.audience{top:1865px;height:529px;background:#fff}
.audience h2{position:absolute;top:110px;width:100%}
.audience .intro{position:absolute;top:160px;width:100%;line-height:24px}
.aud{width:190px;text-align:center}
.aud .ring{margin:0 auto;width:140px;height:140px;border-radius:50%;background:#fff;border:1px solid #e3e7ec;box-shadow:0 4px 14px rgba(0,0,0,.08);display:flex;align-items:center;justify-content:center}
.aud .ring.on{border:6px solid var(--brand);box-shadow:0 0 0 6px rgba(21,101,192,.15)}
.aud p{margin-top:22px;font-size:17px;line-height:22px;color:#333}
.aud p.on{color:var(--brand)}
.arrow{width:36px;height:36px;border-radius:50%;background:#fff;box-shadow:0 1px 6px rgba(0,0,0,.2);display:flex;align-items:center;justify-content:center}

/* team */
.team{top:2394px;height:695px;background:linear-gradient(160deg,#1f73c9 0%,#0f57aa 60%,#0c4c98 100%)}
.team h2{position:absolute;top:118px;width:100%;color:#fff}
.team .sub{position:absolute;top:168px;width:100%;text-align:center;color:#fff;font-size:22px}
.card{width:190px;height:378px;background:#fff;box-shadow:0 6px 18px rgba(0,0,0,.25);text-align:center}
.card .pic{margin:30px auto 0;width:150px;height:206px;background:linear-gradient(180deg,#c8ccd2,#7a838e)}
.card h3{margin-top:20px;font-family:"Roboto",sans-serif;font-weight:400;font-size:15px;color:#333}
.card h3.on{color:var(--brand)}
.card .role{margin-top:6px;font-size:12px;color:var(--grey)}
.card .ic{margin-top:10px;display:flex;justify-content:center;gap:7px}
.card .ic i{display:block;width:9px;height:9px;border-radius:50%;background:#9aa1a9}
.card.on{border-bottom:5px solid var(--brand)}

/* blog */
.blog{top:3089px;height:649px;background:var(--sky)}
.blog h2{position:absolute;top:72px;width:100%}
.post{width:440px;height:262px;background:#fff;border-bottom:6px solid var(--brand);box-shadow:0 3px 12px rgba(0,0,0,.08);text-align:center;padding:70px 40px 0}
.post h3{font-family:"Roboto",sans-serif;font-weight:500;font-size:16px;color:#222}
.post p{margin-top:14px;font-size:12px;line-height:18px;color:#666}
.post a{display:inline-block;margin-top:12px;font-size:13px;color:var(--brand);border-bottom:1px solid var(--brand);text-decoration:none}
.date{width:108px;height:108px;border-radius:50%;background:#fff;border:6px solid #5a5f66;box-shadow:0 0 0 5px #e6eaef;text-align:center;padding-top:12px}
.date b{display:block;font-family:"Roboto",sans-serif;font-weight:500;font-size:40px;line-height:44px;color:var(--brand)}
.date span{font-size:12px;color:#555}
.btn-outline{left:529px;top:525px;width:142px;height:40px;border:1px solid var(--brand);background:#fff;color:var(--brand);font-size:14px;display:flex;align-items:center;justify-content:center}

/* get started */
.start{top:3738px;height:640px;background:linear-gradient(180deg,#1a6bc2,#0f4f9e)}
.start h2{position:absolute;top:100px;width:100%;color:#fff}
.form{left:313px;top:186px;width:645px;height:145px;display:grid;grid-template-columns:320px 325px;grid-template-rows:48px 48px 49px;border:1px solid rgba(255,255,255,.35)}
.field{border-bottom:1px solid rgba(255,255,255,.35);border-right:1px solid rgba(255,255,255,.35);color:rgba(255,255,255,.85);font-size:12px;padding:14px 18px}
.field.msg{grid-column:2;grid-row:1/4;border-right:none;border-bottom:none}
.field.first{background:rgba(0,0,0,.15)}
.btn-dark{left:529px;top:361px;width:145px;height:36px;background:#111;color:#fff;font-family:"Roboto",sans-serif;font-weight:500;font-size:14px;display:flex;align-items:center;justify-content:center}

/* footer */
.footer{top:4256px;height:177px;background:transparent}
.footer .curve{left:0;top:0;width:1200px;height:177px}
.footer .brand{left:142px;top:40px;font-size:30px}
.footer .brand .mark{width:36px;height:36px}
.footer .links{right:142px;top:66px;display:flex;gap:40px;font-family:"Roboto",sans-serif;font-size:13px;color:#222}
.footer .legal{left:142px;right:142px;top:140px;display:flex;justify-content:space-between;font-size:11px;color:#555}
.chat{left:1018px;top:-34px;width:44px;height:44px;border-radius:50%;background:#fff;box-shadow:0 2px 8px rgba(0,0,0,.25);display:flex;align-items:center;justify-content:center;z-index:2}
</style>
</head>
<body>

<!-- Top bar -->
<header class="sec topbar">
  <div class="abs contact">
    <span><svg width="18" height="18" viewBox="0 0 24 24" fill="none" stroke="#fff" stroke-width="2"><path d="M5 3h4l2 5-3 2a11 11 0 0 0 6 6l2-3 5 2v4a2 2 0 0 1-2 2A17 17 0 0 1 3 5a2 2 0 0 1 2-2z"/></svg>+061-555-0142</span>
    <span><svg width="20" height="16" viewBox="0 0 24 18" fill="none" stroke="#fff" stroke-width="2"><rect x="1" y="1" width="22" height="16" rx="2"/><path d="M1 2l11 8 11-8"/></svg>info@vaultmerrow.com.au</span>
  </div>
  <div class="abs follow">Follow Us on
    <i class="social"></i><i class="social"></i><i class="social"></i><i class="social"></i>
  </div>
</header>

<!-- Navigation -->
<nav class="sec nav">
  <div class="abs brand"><i class="mark"></i>Vault Merrow</div>
  <div class="abs menu">
    <a class="active">HOME</a><a>ABOUT</a><a>SERVICES</a><a>RESOURCES</a><a>BLOG</a><a>CONTACT US</a>
  </div>
</nav>

<!-- Hero -->
<section class="sec hero">
  <div class="abs art" role="img" aria-label="Glowing blue digital network over the curve of the earth"></div>
  <svg class="abs" style="left:0;top:0" width="1200" height="576" viewBox="0 0 1200 576">
    <path d="M0 576 L0 520 Q620 640 1200 380 L1200 576 Z" fill="#fff"/>
  </svg>
  <h1 class="abs">Because we care, we're security aware</h1>
  <div class="abs btn-light">Contact Us Today</div>
  <div class="abs dots"><i></i><i class="on"></i><i></i></div>
</section>

<!-- About -->
<section class="sec about">
  <div class="abs photo" role="img" aria-label="Smiling businessman in a suit working on a laptop"></div>
  <div class="abs photo-tag">Vault Merrow</div>
  <div class="abs head">About <span class="brand"><i class="mark"></i>Vault Merrow</span></div>
  <div class="abs copy">
    <p><b>Vault Merrow</b> keeps critical records safe, recoverable and ready when it matters. Teams lean on our services to protect data against loss, outage and attack.</p>
    <p>We plan backup, recovery and continuity around the way your business runs, so systems come back quickly and nothing important is lost along the way.</p>
    <p>From small offices to government bodies, we help leaders understand their risk, meet compliance needs and build habits that keep information secure.</p>
    <p>Our specialists monitor, test and improve each plan over time, giving you clear reports and practical steps rather than jargon and guesswork.</p>
    <p class="cta">Get the support you need now. <span>Contact our 24/7 support line to get started.</span></p>
  </div>
</section>

<!-- Services -->
<section class="sec services">
  <h2 class="title">SERVICES</h2>
  <p class="intro"><b>Vault Merrow</b> brings together the tools and people needed to keep business data protected and available.<br>Every service is tailored to your systems, your risks and the way your teams work each day.</p>

  <div class="abs svc-label l on" style="left:65px;top:228px">Data Management<br>Platforms</div>
  <div class="abs svc-icon on" style="left:340px;top:215px">
    <svg width="46" height="46" viewBox="0 0 48 48" fill="none" stroke="#1565c0" stroke-width="2.5"><path d="M14 30a8 8 0 0 1 1-16 11 11 0 0 1 21 3 7 7 0 0 1-1 13z"/><path d="M24 30v10M18 40h12"/></svg>
  </div>
  <div class="abs svc-label l" style="left:65px;top:392px">Data Management<br>Services</div>
  <div class="abs svc-icon" style="left:340px;top:378px">
    <svg width="46" height="46" viewBox="0 0 48 48" fill="none" stroke="#444" stroke-width="2.5"><ellipse cx="22" cy="12" rx="12" ry="5"/><path d="M10 12v22c0 3 5 5 12 5M34 12v12M10 23c0 3 5 5 12 5"/><circle cx="36" cy="36" r="6"/></svg>
  </div>

  <div class="abs centre-mark">Vault Merrow</div>

  <div class="abs svc-icon" style="left:740px;top:215px">
    <svg width="46" height="46" viewBox="0 0 48 48" fill="none" stroke="#444" stroke-width="2.5"><circle cx="18" cy="18" r="7"/><circle cx="32" cy="32" r="6"/><path d="M18 8v3M18 25v3M8 18h3M25 18h3M32 23v2M32 39v2M23 32h2M39 32h2"/></svg>
  </div>
  <div class="abs svc-label" style="left:878px;top:228px">Industry<br>Solutions</div>
  <div class="abs svc-icon" style="left:740px;top:378px">
    <svg width="46" height="46" viewBox="0 0 48 48" fill="none" stroke="#444" stroke-width="2.5"><rect x="8" y="10" width="32" height="22" rx="2"/><path d="M18 40h12M24 32v8"/><rect x="19" y="19" width="10" height="8"/><path d="M21 19v-3a3 3 0 0 1 6 0v3"/></svg>
  </div>
  <div class="abs svc-label" style="left:878px;top:392px">Ransomware<br>Protection</div>
</section>

<!-- Who we serve -->
<section class="sec audience">
  <h2 class="title">TO WHOM WE SERVE</h2>
  <p class="intro">We support the people responsible for keeping data safe, from risk teams to senior leaders,<br>helping each one plan ahead, respond quickly and recover with confidence.</p>
  <div class="abs arrow" style="left:74px;top:289px"><svg width="10" height="12" viewBox="0 0 10 12"><path d="M8 1L2 6l6 5" fill="none" stroke="#555" stroke-width="2"/></svg></div>
  <div class="abs aud" style="left:118px;top:237px"><div class="ring"><svg width="56" height="56" viewBox="0 0 48 48" fill="none" stroke="#444" stroke-width="2"><path d="M20 8L4 38h32z"/><path d="M20 18v10M20 32v2"/><circle cx="36" cy="34" r="7"/></svg></div><p>Risk Managers</p></div>
  <div class="abs aud" style="left:313px;top:237px"><div class="ring"><svg width="56" height="56" viewBox="0 0 48 48" fill="none" stroke="#444" stroke-width="2"><path d="M24 5l15 6v11c0 10-7 17-15 21C16 39 9 32 9 22V11z"/><path d="M17 24l5 5 9-10"/></svg></div><p>Information<br>Security</p></div>
  <div class="abs aud" style="left:505px;top:237px"><div class="ring on"><svg width="56" height="56" viewBox="0 0 48 48" fill="none" stroke="#1565c0" stroke-width="2"><rect x="10" y="10" width="28" height="28" rx="3"/><path d="M16 4v6M24 4v6M32 4v6M16 38v6M24 38v6M32 38v6M4 16h6M4 24h6M4 32h6M38 16h6M38 24h6M38 32h6"/><rect x="19" y="23" width="10" height="8"/><path d="M21 23v-3a3 3 0 0 1 6 0v3"/></svg></div><p class="on">Cyber Security<br>Professionals</p></div>
  <div class="abs aud" style="left:697px;top:237px"><div class="ring"><svg width="56" height="56" viewBox="0 0 48 48" fill="none" stroke="#444" stroke-width="2"><circle cx="24" cy="13" r="6"/><path d="M14 28a10 10 0 0 1 20 0"/><rect x="8" y="28" width="32" height="6"/><path d="M12 34v8M36 34v8"/></svg></div><p>Chief Data<br>Technicians</p></div>
  <div class="abs aud" style="left:889px;top:237px"><div class="ring"><svg width="56" height="56" viewBox="0 0 48 48" fill="none" stroke="#444" stroke-width="2"><circle cx="24" cy="14" r="7"/><path d="M10 42c0-9 6-15 14-15s14 6 14 15z"/><path d="M24 27v15M20 30l4 4 4-4"/></svg></div><p>Digital Officers</p></div>
  <div class="abs arrow" style="left:1090px;top:289px"><svg width="10" height="12" viewBox="0 0 10 12"><path d="M2 1l6 5-6 5" fill="none" stroke="#555" stroke-width="2"/></svg></div>
  <svg class="abs" style="left:0;top:440px" width="1200" height="89" viewBox="0 0 1200 89"><path d="M0 0 L0 89 L180 89 Z" fill="#8f959c"/></svg>
</section>

<!-- Team -->
<section class="sec team">
  <h2 class="title">OUR TEAM</h2>
  <p class="sub">Our Bestest Team Members.</p>
  <div class="abs arrow" style="left:142px;top:383px;width:32px;height:32px"><svg width="10" height="12" viewBox="0 0 10 12"><path d="M8 1L2 6l6 5" fill="none" stroke="#555" stroke-width="2"/></svg></div>
  <div class="abs card" style="left:192px;top:230px"><div class="pic" role="img" aria-label="Portrait of team member in casual shirt"></div><h3>AVERY LANE</h3><div class="role">Designation Here</div><div class="ic"><i></i><i></i><i></i><i></i></div></div>
  <div class="abs card on" style="left:420px;top:230px"><div class="pic" role="img" aria-label="Portrait of team member in business jacket"></div><h3 class="on">MARA QUELL</h3><div class="role">Designation Here</div><div class="ic"><i></i><i></i><i></i><i></i></div></div>
  <div class="abs card" style="left:647px;top:230px"><div class="pic" role="img" aria-label="Portrait of team member in suit"></div><h3>THEO BRANDT</h3><div class="role">Designation Here</div><div class="ic"><i></i><i></i><i></i><i></i></div></div>
  <div class="abs card" style="left:875px;top:230px"><div class="pic" role="img" aria-label="Portrait of team member in shirt"></div><h3>OWEN PIKE</h3><div class="role">Designation Here</div><div class="ic"><i></i><i></i><i></i><i></i></div></div>
  <div class="abs arrow" style="left:1022px;top:383px;width:32px;height:32px"><svg width="10" height="12" viewBox="0 0 10 12"><path d="M2 1l6 5-6 5" fill="none" stroke="#555" stroke-width="2"/></svg></div>
</section>

<!-- Blog -->
<section class="sec blog">
  <svg class="abs" style="left:0;top:0" width="1200" height="649" viewBox="0 0 1200 649">
    <path d="M850 0 L1200 0 L1200 62 Z" fill="#8f959c"/>
    <path d="M0 580 L0 649 L300 649 Z" fill="#8f959c"/>
  </svg>
  <h2 class="title">LATEST BLOG POSTS</h2>
  <div class="abs arrow" style="left:84px;top:326px;width:32px;height:32px"><svg width="10" height="12" viewBox="0 0 10 12"><path d="M8 1L2 6l6 5" fill="none" stroke="#555" stroke-width="2"/></svg></div>
  <div class="abs post" style="left:142px;top:211px"><h3>The point of using Lorem Ipsum</h3><p>"Keeping a tested backup plan in place means a sudden outage becomes a short pause, not a crisis, for your whole team and your customers."</p><a>Learn More</a></div>
  <div class="abs date" style="left:307px;top:143px"><b>12</b><span>Feb 2019</span></div>
  <div class="abs post" style="left:618px;top:211px"><h3>The point of using Lorem Ipsum</h3><p>"Ransomware keeps changing, so the best defence is a layered plan with offline copies, fast restores and people who know the steps."</p><a>Learn More</a></div>
  <div class="abs date" style="left:780px;top:143px"><b>06</b><span>Feb 2019</span></div>
  <div class="abs arrow" style="left:1078px;top:326px;width:32px;height:32px"><svg width="10" height="12" viewBox="0 0 10 12"><path d="M2 1l6 5-6 5" fill="none" stroke="#555" stroke-width="2"/></svg></div>
  <div class="abs btn-outline">View All</div>
</section>

<!-- Get started -->
<section class="sec start">
  <div class="abs" style="left:0;top:0;width:1200px;height:640px;opacity:.25;background:linear-gradient(120deg,#4a90d9,#0b3f86)" role="img" aria-label="Blurred team working together in an office"></div>
  <h2 class="title">LET'S GET STARTED</h2>
  <div class="abs form">
    <div class="field first">Your Name</div>
    <div class="field msg">Your Message</div>
    <div class="field">Your Email</div>
    <div class="field" style="border-bottom:none">Your Contact Number</div>
  </div>
  <div class="abs btn-dark">Submit</div>
</section>

<!-- Footer -->
<footer class="sec footer" style="overflow:visible">
  <svg class="abs curve" viewBox="0 0 1200 177" preserveAspectRatio="none">
    <path d="M0 20 Q600 -20 1200 20 L1200 177 L0 177 Z" fill="#fff"/>
  </svg>
  <div class="abs chat"><svg width="22" height="20" viewBox="0 0 24 22"><path d="M3 3h18v12H10l-5 4v-4H3z" fill="#1565c0"/></svg></div>
  <div class="abs brand"><i class="mark"></i>Vault Merrow</div>
  <div class="abs links"><span>HOME</span><span>ABOUT</span><span>SERVICES</span><span>RESOURCES</span><span>BLOG</span><span>CONTACT US</span></div>
  <div class="abs legal"><span>Copyright 2019 @ Vault Merrow. All Rights Reserved.</span><span>Terms of services / Privacy Policy</span></div>
</footer>

</body>
</html>
```